Church Website with Home Page and Member Sermon Library

I am in need of an updated design for our church website. This will include 4 pages (outlined below). We are a conservative, evangelical, Christian church. The site should be modern and clean, while still reflecting our conservative values. I already have a logo for our church, and I want the site to incorporate the logo, and match the logo/branding. Stock photos are allowed if needed, but I have uploaded some images of our church and would prefer those images to be used if possible. Any stock photos used should not include any people in the photos (scenery, nature, buildings, animals, etc. are fine).

The site will need 4 pages: Home, Support Us (Donate), Login, and Recording Library.

Page 1: Home
The home page should include the following sections:

- Navigation: Should include links to each section of the home page plus a "listen live" link which will take the user to a live-streaming site and a "support us" link which will take the user to a support/donate page.

- Announcements: Can be either a banner or some other design, but there needs to be some way for us to post announcements for visitors to see. I'm open for creative ideas in this section, but would like it not to take up a lot of room on the page.

- About Us: Should include address, service times (see attached document), and information about the church.

- Pastor Bio: A section that introduces our pastor and gives a short bio about our pastor. Would like this section to include a picture of our pastor. Somewhere in this section I would like to include this Bible reference: "And I will give you pastors according to mine heart, which shall feed you with knowledge and understanding. Jer 3:15 LPW"

- Articles of Faith (What We Believe): This should include several sub-sections each with a heading, body, and possibly 1 or more scripture references. I have attached a document to the brief that includes our articles of faith. Feel free to be creative with this section in how you lay these out and format them.

- Support Us: A small section that explains what kind of support someone can give and a link to a donation page. The link can say something like "Support Us" or "Donate Now".

- Contact form: A contact form that allows the visitor to send us a message. The contact form should ask for name, email, phone, and message.

- Footer: A footer that will be displayed on all pages of the site. This should include at a minimum a link to the home page (or a link to each individual section in the home page if you prefer), a link to "listen live", a link to "support us", a link to "contact us" (or you can put the contact form directly in the footer if you prefer), the address, and a "member login" link.

Page 2: Support Us
The donation page should include a form the visitor can fill out to make a donation. We will embed a third party form later. For this design, please just mock out the design with a basic form asking for name, phone, and email.

Page 3: Login
The recording library (detailed below) will require members to login with a shared numeric code before accessing the page. We need a design for a login screen. The screen should include navigation/footer just like all other pages, but the body of the login page will consist only of a form that asks the user to enter the access code and then a "login" button.

Page 4: Recording Library

The library page is a member-only page that will require a shared, numeric pass code to access. On this page, members will be able to access a filterable list of past sermons. The page by default should display most recent sermons, but should also include a search form that allows the member to filter the sermon list to find a particular sermon. The search form should allow the user to select a filter type (e.g. Speaker name, date, event, etc.) and type in a value to search. They should be able to add multiple filters and remove filters that have been added. Each sermon that is displayed in the result list should include basic information such as title, date, speaker, tags, etc. along with a download icon, and an embedded audio player where they can click a play button to stream it on-demand. Each sermon should also have clickable tags associated with it that can be used to find related sermons.
Updates

I have uploaded several images of our church. Feel free to incorporate these into your design if possible.

Target Market(s)

Church Members

Industry/Entity Type

Religion

Number of Pages Required

4 page

Font styles to use
Sans Serif

Colors

Designer to choose colors to be used in the design.

Requirements
Must have
• Must incorporate the logo (attached)
Nice to have
• Would like the design to incorporate pictures of our church (attached) instead of stock photos if possible.
Should not have
• Please avoid an overly cluttered design. Stock photos used should not include any people in the photos.

```html
<!DOCTYPE html>
<html lang="en">
<head>
<meta charset="utf-8">
<title>Cedar Grove Chapel – Member Login</title>
<link rel="stylesheet" href="https://fonts.googleapis.com/css2?family=Outfit:wght@300;400;500;700;800&display=swap">
<style>
  :root {
    --ink-dark: #1f1f1b;
    --white: #ffffff;
    --text-dark: #1e1e1e;
    --text-muted: #8d8d8d;
    --field-bg: #ebebeb;
    --field-border: #cfcfcf;
    --brand-teal: #0bbcd6;
    --brand-green: #a3e85a;
    --brand-logo: #3f8f5a;
    --link-blue: #1ab8d4;
    --sand-light: #6a5c4e;
    --sand-dark: #3c342c;
  }
  * { box-sizing: border-box; margin: 0; padding: 0; }
  html, body { width: 1200px; height: 1125px; overflow: hidden; }
  body {
    position: relative;
    background: var(--ink-dark);
    font-family: "Outfit", sans-serif;
    color: var(--white);
  }
  .hero { position: absolute; left: 0; top: 0; width: 1200px; height: 650px; }
  .hero-photo {
    position: absolute; left: 0; top: 0; width: 620px; height: 650px;
    background:
      linear-gradient(90deg, rgba(31,31,27,0) 60%, var(--ink-dark) 100%),
      radial-gradient(ellipse at 30% 40%, var(--sand-light) 0%, var(--sand-dark) 75%);
  }
  .hero-title {
    position: absolute; left: 120px; top: 86px;
    font-weight: 800; font-size: 60px; line-height: 76px;
    text-transform: uppercase; letter-spacing: -0.5px;
  }
  .hero-lead {
    position: absolute; left: 119px; top: 470px;
    font-weight: 300; font-size: 25px; line-height: 30px;
  }
  .login-card {
    position: absolute; left: 617px; top: 16px; width: 566px; height: 618px;
    background: var(--white); border-radius: 12px;
  }
  .brand {
    position: absolute; left: 98px; top: 98px;
    display: flex; align-items: center; gap: 12px;
    font-weight: 500; font-size: 26px; color: var(--brand-logo);
  }
  .brand-mark { width: 34px; height: 34px; background: var(--brand-teal); }
  .field-label {
    position: absolute; left: 96px; top: 239px;
    font-weight: 700; font-size: 19px; color: var(--text-dark);
  }
  .code-input {
    position: absolute; left: 93px; top: 275px; width: 390px; height: 59px;
    background: var(--field-bg); border: 1px solid var(--field-border);
  }
  .field-hint {
    position: absolute; left: 93px; top: 345px;
    font-size: 17px; font-weight: 400; color: var(--text-muted);
  }
  .login-button {
    position: absolute; left: 93px; top: 381px; width: 390px; height: 59px;
    background: linear-gradient(90deg, var(--brand-teal) 0%, #6fdc8a 60%, var(--brand-green) 100%);
    display: flex; align-items: center; justify-content: center;
    font-weight: 800; font-size: 20px; color: var(--text-dark); letter-spacing: 0.3px;
  }
  .legal-note {
    position: absolute; left: 93px; top: 533px; width: 400px;
    font-size: 15px; line-height: 18px; font-weight: 300; color: var(--text-muted);
  }
  .legal-note span { text-decoration: underline; }

  .site-footer { position: absolute; left: 0; top: 650px; width: 1200px; height: 475px; }
  .footer-col { position: absolute; top: 77px; }
  .footer-heading { font-weight: 800; font-size: 19px; text-transform: uppercase; }
  .footer-links { list-style: none; margin-top: 20px; }
  .footer-links li { font-size: 20px; font-weight: 300; height: 49px; line-height: 24px; }
  .col-who { left: 83px; }
  .col-info { left: 275px; }
  .col-help { left: 417px; }
  .col-find { left: 595px; }
  .contact-text { margin-top: 20px; font-size: 20px; font-weight: 300; line-height: 24px; }
  .col-find .footer-heading.second { margin-top: 10px; }
  .contact-email { margin-top: 22px; font-size: 20px; font-weight: 300; text-decoration: underline; }
  .social-list { display: flex; gap: 50px; margin-top: 28px; }
  .social-dot { width: 31px; height: 31px; border-radius: 50%; background: var(--white); }
  .copyright {
    position: absolute; left: 83px; top: 410px;
    font-size: 20px; font-weight: 300;
  }
  .copyright span { color: var(--link-blue); text-decoration: underline; }
</style>
</head>
<body>
  <section class="hero">
    <div class="hero-photo" role="img" aria-label="Footprints in warm brown sand"></div>
    <h1 class="hero-title">Join our<br>recording<br>library of<br>latest<br>sermons</h1>
    <p class="hero-lead">Get access to thousands of<br>sermons by different speakers.</p>

    <div class="login-card">
      <div class="brand"><span class="brand-mark"></span>Cedar Grove Chapel</div>
      <label class="field-label">Enter numeric code</label>
      <div class="code-input"></div>
      <p class="field-hint">Minimum 6 numeric characters</p>
      <div class="login-button">LOG IN</div>
      <p class="legal-note">By logging in, I confirm that I have read and agree to the Cedar Grove Chapel <span>Terms of Service</span>, <span>Privacy Policy</span>, and to receive email and updates.</p>
    </div>
  </section>

  <footer class="site-footer">
    <div class="footer-col col-who">
      <h2 class="footer-heading">Who we are</h2>
      <ul class="footer-links"><li>About us</li><li>Ministries</li><li>Events</li></ul>
    </div>
    <div class="footer-col col-info">
      <h2 class="footer-heading">Info</h2>
      <ul class="footer-links"><li>Careers</li><li>Community</li><li>Blog</li><li>Press</li></ul>
    </div>
    <div class="footer-col col-help">
      <h2 class="footer-heading">Help</h2>
      <ul class="footer-links"><li>Contact us</li><li>FAQ</li><li>Legal &amp; Privacy</li></ul>
    </div>
    <div class="footer-col col-find">
      <h2 class="footer-heading">Find us at</h2>
      <p class="contact-text">(555) 214-0387<br>Maple Ridge Rd, Fairview, Ohio<br>(OH), 45001</p>
      <h2 class="footer-heading second">Write to us</h2>
      <p class="contact-email">hello@cedargrovechapel.org</p>
      <div class="social-list">
        <span class="social-dot" aria-label="Video channel"></span>
        <span class="social-dot" aria-label="Social page"></span>
        <span class="social-dot" aria-label="Microblog"></span>
        <span class="social-dot" aria-label="Messenger"></span>
      </div>
    </div>
    <p class="copyright">© 2021 Lumen. All Rights Reserved. <span>Privacy Policy</span></p>
  </footer>
</body>
</html>
```